Business Card For Halvenmoor Financial Consulting

Hi, I would like a business card designed. Bold, modern.
Please use the same design as the logo. I have also attached the website design to see the overall theme.
Wordmark Font
Color: Hex: #01AEF7

```html
<!DOCTYPE html>
<html lang="en">
<head>
<meta charset="utf-8">
<title>Halvenmoor Financial Consulting – Business Card</title>
<link href="https://fonts.googleapis.com/css2?family=Montserrat:wght@800&family=Open+Sans:wght@400;700&display=swap" rel="stylesheet">
<style>
  :root {
    --backdrop: #222222;
    --card-navy: #0a4569;
    --accent-blue: #01aef7;
    --edge-blue: #3aa6e0;
    --text-white: #ffffff;
    --divider: rgba(255,255,255,0.75);
  }
  * { margin: 0; padding: 0; box-sizing: border-box; }
  html, body {
    width: 1200px; height: 780px; overflow: hidden;
    background: var(--backdrop);
  }
  .stage { position: relative; width: 1200px; height: 780px; }
  .card {
    position: absolute; top: 236px;
    width: 540px; height: 308px;
    background: var(--card-navy);
    border-left: 6px solid var(--edge-blue);
    box-shadow: 0 10px 24px rgba(0,0,0,0.55);
    overflow: hidden;
  }
  .card--front { left: 40px; }
  .card--back { left: 620px; }

  .brand {
    position: absolute; display: flex; align-items: center; gap: 14px;
  }
  .brand__square {
    border: 4px solid var(--accent-blue);
    flex: none;
  }
  .brand__name {
    font-family: "Montserrat", sans-serif; font-weight: 800;
    color: var(--text-white); text-transform: uppercase;
    line-height: 1.05; letter-spacing: 1px;
  }
  .card--front .brand { left: 70px; top: 112px; }
  .card--front .brand__square { width: 64px; height: 64px; }
  .card--front .brand__name { font-size: 33px; }

  .card--back .brand { left: 30px; top: 190px; }
  .card--back .brand__square { width: 40px; height: 40px; border-width: 3px; }
  .card--back .brand__name { font-size: 20px; }

  .divider {
    position: absolute; left: 290px; top: 40px;
    width: 1px; height: 228px; background: var(--divider);
  }
  .contact {
    position: absolute; left: 312px; top: 48px; right: 16px;
    font-family: "Open Sans", sans-serif; color: var(--text-white);
  }
  .contact__name {
    font-weight: 700; font-size: 21px; color: var(--accent-blue); line-height: 1.1;
  }
  .contact__role { font-size: 12.5px; margin-bottom: 16px; }
  .contact__address { font-size: 12.5px; line-height: 1.35; margin-bottom: 14px; }
  .contact__list { list-style: none; font-size: 12.5px; line-height: 1.55; }
  .contact__list li { display: flex; align-items: center; gap: 8px; }
  .contact__list svg { width: 12px; height: 12px; flex: none; }
</style>
</head>
<body>
<main class="stage">
  <section class="card card--front" aria-label="Card front">
    <div class="brand">
      <span class="brand__square"></span>
      <span class="brand__name">Halvenmoor<br>Consulting</span>
    </div>
  </section>

  <section class="card card--back" aria-label="Card back">
    <div class="brand">
      <span class="brand__square"></span>
      <span class="brand__name">Halvenmoor<br>Consulting</span>
    </div>
    <span class="divider"></span>
    <div class="contact">
      <p class="contact__name">Lena Varhola</p>
      <p class="contact__role">Managing Director</p>
      <p class="contact__address">1480 Ridgeline Ave. Suite 310<br>Fort Worth, TX 76104</p>
      <ul class="contact__list">
        <li>
          <svg viewBox="0 0 24 24" aria-hidden="true"><path fill="#01AEF7" d="M6.6 10.8a15 15 0 0 0 6.6 6.6l2.2-2.2c.3-.3.7-.4 1-.2 1.1.4 2.3.6 3.6.6.6 0 1 .4 1 1V20c0 .6-.4 1-1 1A17 17 0 0 1 3 4c0-.6.4-1 1-1h3.5c.6 0 1 .4 1 1 0 1.3.2 2.5.6 3.6.1.3 0 .7-.2 1z"/></svg>
          (555) 214-0386
        </li>
        <li>
          <svg viewBox="0 0 24 24" aria-hidden="true"><rect x="2" y="5" width="20" height="14" rx="1.5" fill="none" stroke="#01AEF7" stroke-width="2"/><path d="M2.5 6l9.5 7 9.5-7" fill="none" stroke="#01AEF7" stroke-width="2"/></svg>
          info@halvenmoor.com
        </li>
        <li>
          <svg viewBox="0 0 24 24" aria-hidden="true"><circle cx="12" cy="12" r="9.5" fill="none" stroke="#01AEF7" stroke-width="2"/><path d="M2.5 12h19M12 2.5c3 3 3 16 0 19M12 2.5c-3 3-3 16 0 19" fill="none" stroke="#01AEF7" stroke-width="1.6"/></svg>
          www.halvenmoor.com
        </li>
      </ul>
    </div>
  </section>
</main>
</body>
</html>
```